Roofing company in Toronto, Canada needs a logo design and business card design

We need a business card and logo created for our company. Our company is "KLV Roofing" which provides roofing services for commercial and residential customers. We serve customers in the Greater Toronto Area (in Canada) thus the name KLV.

We want the logo and business card to be a modern design displaying professionalism and quality in the work. We would prefer rounded corners for the business cards but are open to other ideas. The cards should be pleasant and appealing to customers.

Target Market(s)

Commercial and Residential customers

Industry/Entity Type

Roofing

Contact Information for Business Card

Logo Text

KLV Roofing

Requirements
Nice to have
• Colours that are pleasing to the eye but at the same time should stand out from other business cards. If the design can incorporate the name of KLV Roofing and the actual concept of roofing that would be nice.
Should not have
• Do not want the business cards or logo to be childish looking. Need to look professionally designed.

```html
<!DOCTYPE html>
<html lang="en">
<head>
<meta charset="utf-8">
<title>KLV Roofing — Business Card</title>
<link href="https://fonts.googleapis.com/css2?family=Open+Sans:wght@400;600;700&display=swap" rel="stylesheet">
<style>
  :root {
    --backdrop: #3b3532;
    --card: #0f0f0f;
    --gold: #e9a913;
    --light: #ececec;
    --rule: #3a3a3a;
  }
  * { box-sizing: border-box; margin: 0; padding: 0; }
  html, body {
    width: 1200px; height: 844px; overflow: hidden;
    background: var(--backdrop);
    font-family: "Open Sans", Arial, sans-serif;
  }
  .stage {
    position: relative; width: 1200px; height: 844px;
    display: flex; align-items: center; justify-content: center; gap: 40px;
  }
  .card {
    position: relative; width: 540px; height: 310px;
    background: var(--card); border-radius: 10px;
    box-shadow: 0 10px 30px rgba(0,0,0,.45);
  }
  .wordmark {
    position: absolute; left: 0; right: 0;
    display: flex; align-items: center; justify-content: center; gap: 10px;
    color: var(--gold); font-weight: 700; letter-spacing: 1px; white-space: nowrap;
  }
  .wordmark-square { width: 12px; height: 12px; background: var(--gold); }
  .card-front .wordmark { top: 48px; font-size: 44px; }
  .card-back .wordmark { top: 110px; font-size: 52px; }
  .identity {
    position: absolute; right: 288px; top: 170px; text-align: right; color: var(--light);
    white-space: nowrap;
  }
  .identity-name { color: var(--gold); font-size: 22px; font-weight: 400; line-height: 1.1; }
  .identity-role { font-size: 14px; margin-top: 2px; }
  .identity-address { font-size: 15px; line-height: 1.2; margin-top: 16px; }
  .divider {
    position: absolute; left: 268px; top: 168px; width: 1px; height: 112px; background: var(--rule);
  }
  .contacts {
    position: absolute; left: 286px; top: 170px; list-style: none; color: var(--light); font-size: 14px;
    white-space: nowrap;
  }
  .contacts li { display: flex; align-items: center; gap: 10px; height: 22px; }
  .contacts svg { width: 12px; height: 12px; fill: var(--gold); flex: none; }
  .contacts .icon-mail { fill: none; stroke: var(--gold); stroke-width: 1.5; }
</style>
</head>
<body>
<main class="stage">
  <section class="card card-front" aria-label="Card front">
    <div class="wordmark"><span class="wordmark-square"></span>KLV Roofing</div>
    <div class="identity">
      <p class="identity-name">Marcus Bell</p>
      <p class="identity-role">Managing Director</p>
      <p class="identity-address">88 Harbour Lane, Unit 4<br>Toronto, ON M5J 1A7</p>
    </div>
    <div class="divider"></div>
    <ul class="contacts">
      <li><svg viewBox="0 0 12 12"><path d="M2 1l2.2-.3 1 2.6-1.3 1a6 6 0 0 0 3 3l1-1.3 2.6 1L10.2 10C5.5 10.3 1.7 6.5 2 1z"/></svg>(416)-555-0142</li>
      <li><svg viewBox="0 0 12 12"><rect x="1" y="4" width="10" height="7" rx="1"/><rect x="3" y="1" width="6" height="3"/></svg>647-555-0198</li>
      <li><svg class="icon-mail" viewBox="0 0 12 12"><path d="M1 3h10v7H1z M1 3l5 4 5-4"/></svg>hello@klvroofs.ca</li>
      <li><svg viewBox="0 0 12 12"><circle cx="6" cy="6" r="5"/></svg>www.klvroofs.ca</li>
    </ul>
  </section>
  <section class="card card-back" aria-label="Card back">
    <div class="wordmark"><span class="wordmark-square"></span>KLV Roofing</div>
  </section>
</main>
</body>
</html>
```